PHGCCUL re-branding website and logo

We are looking for a new webpage design and logo our current page address is www.phgccul-example.org. We want to create a new design using PHGCCUL Pinewood and Harbour Growers Co-operative Credit Union limited and another with the purposed new name PHFC Pinewood and Harbour Financial Co-operative, the color scheme is purple and burnt orange. Our new logo and webpage should communicate change and growth purposed theme continuing our legacy here to server past, present and future generations. Our idea for the logo is a live shot of hands of different ages in a circle holding a tree

Target Market(s)

Everyone

Contact Information for Business Card

Company Name
Telephone number
Address
slot to enter employee info

Logo Text

(P & H) Pinewood And Harbour Financial Co-operative

Coding

Coded - Design and coding required

Number of Pages Required

2 page

Colors
f37122
fbed22
6b449b

Requirements
Must have
• links for social media

```html
<!DOCTYPE html>
<html lang="en">
<head>
<meta charset="utf-8">
<title>Pinewood and Harbour Financial Co-operative</title>
<link rel="stylesheet" href="https://fonts.googleapis.com/css2?family=Mulish:wght@400;600;700&display=swap">
<style>
:root{
  --black:#000;
  --orange:#f37122;
  --yellow:#fbed22;
  --purple:#6b449b;
  --grey-bg:#eeeeee;
  --text:#333;
  --muted:#8a8a8a;
  --white:#fff;
}
*{box-sizing:border-box;margin:0;padding:0}
html,body{width:1200px;height:2736px;overflow:hidden}
body{font-family:"Mulish",sans-serif;color:var(--text);background:var(--white);position:relative}
.btn{display:inline-block;background:var(--orange);color:var(--white);font-size:12px;text-transform:uppercase;padding:0 19px;height:31px;line-height:31px;text-align:center}

/* header */
.site-header{position:absolute;left:0;top:0;width:1200px;height:140px;background:var(--black);color:var(--white)}
.brand-name{font-size:20px;font-weight:400;color:var(--white);line-height:1.3;width:230px}
.site-header .brand-name{position:absolute;left:137px;top:40px}
.header-phone{position:absolute;right:116px;top:24px;font-size:22px;display:flex;align-items:center;gap:6px}
.main-nav{position:absolute;right:111px;top:80px;display:flex;gap:31px;font-size:16px;text-transform:uppercase}

/* hero */
.hero{position:absolute;left:0;top:140px;width:1200px;height:493px;background:linear-gradient(100deg,#c9b6a8 0%,#e8ddd6 30%,#f3e1dc 55%,#ece8e4 80%,#d9d4cf 100%)}
.hero-caption{position:absolute;left:120px;top:134px;width:464px;height:200px;background:var(--orange);opacity:.93;color:var(--white);padding:46px 30px 0 30px}
.hero-caption .kicker{font-size:22px;font-weight:600;text-transform:uppercase;white-space:nowrap}
.hero-caption h1{font-size:27px;font-weight:600;text-transform:uppercase;line-height:1.2;white-space:nowrap}
.hero-caption p{font-size:13px;line-height:1.6;margin-top:6px}
.hero-dots{position:absolute;left:557px;top:466px;display:flex;gap:8px}
.hero-dots span{width:14px;height:14px;border-radius:50%;background:var(--white)}
.hero-dots span:first-child{background:transparent;border:2px solid var(--white)}

/* quick actions */
.quick-actions{position:absolute;left:0;top:633px;width:1200px;height:343px;display:flex;justify-content:center}
.action{width:346px;text-align:center;padding-top:34px}
.action svg{height:88px}
.action h2{font-size:25px;font-weight:400;color:#222;margin-top:10px}
.action p{font-size:12px;color:var(--muted);line-height:1.5;width:290px;margin:6px auto 20px}

/* promo band */
.promo-band{position:absolute;left:0;top:976px;width:1200px;height:425px;background:var(--purple)}
.promo-card{position:absolute;top:69px;width:486px;height:288px;background:var(--white);overflow:hidden}
.promo-card.credit-union{left:111px}
.promo-card.products{left:607px}
.promo-photo{position:absolute;left:0;top:0;width:278px;height:288px}
.credit-union .promo-photo{background:linear-gradient(135deg,#8fae6a,#c9b79c 60%,#6f86a8)}
.products .promo-photo{width:300px;background:linear-gradient(135deg,#d9d3cb,#c9a595 50%,#d6493a)}
.products .promo-fill{position:absolute;inset:0;background:var(--yellow);clip-path:polygon(287px 0,486px 0,486px 288px,228px 288px)}
.promo-body{position:absolute;left:282px;top:54px;width:190px}
.products .promo-body{left:280px}
.promo-body h3{font-size:26px;font-weight:400;line-height:1.2;color:#222}
.promo-body p{font-size:12px;line-height:1.5;color:var(--muted);margin:10px 0 12px}

/* notice */
.notice{position:absolute;left:0;top:1401px;width:1200px;height:470px;background:var(--grey-bg)}
.notice-photo{position:absolute;left:657px;top:10px;width:420px;height:460px;background:linear-gradient(180deg,#2b211d 0%,#c99d86 35%,#ece7e3 70%,#f3f1ef 100%);border-radius:200px 200px 0 0}
.notice-text{position:absolute;left:108px;top:108px;width:540px}
.notice-text h2{font-size:36px;font-weight:400;color:#333}
.notice-text .lead{font-size:20px;line-height:1.35;margin-top:8px;color:#222}
.notice-text .body{font-size:14px;line-height:1.6;color:var(--muted);margin:24px 0 26px}
.notice-text .btn{background:var(--purple);height:37px;line-height:37px;padding:0 25px;font-size:14px}

/* rates & news */
.rates{position:absolute;left:113px;top:1943px;width:462px}
.rates h2,.news h2{font-size:28px;font-weight:400;color:#333;margin-bottom:18px}
.rate{height:67px;background:var(--yellow);display:flex;align-items:center;padding:0 20px 0 16px;margin-bottom:9px}
.rate svg{width:40px;height:36px;flex:none}
.rate .label{margin-left:18px;flex:1;font-size:17px;color:#222;line-height:1.1}
.rate .label small{display:block;font-size:12px;color:#555}
.rate .value{font-size:17px;color:#222}
.news{position:absolute;left:625px;top:1943px;width:480px}
.news-item{display:flex;gap:22px;margin-bottom:34px}
.news-thumb{width:130px;height:130px;border-radius:50%;flex:none}
.news-item:nth-child(2) .news-thumb{background:linear-gradient(135deg,#1d2b45,#c9a88c 55%,#2f3a55)}
.news-item:nth-child(3) .news-thumb{background:linear-gradient(135deg,#c7cfd8,#5a4a3e 55%,#e2ddd6)}
.news-item h3{font-size:21px;font-weight:400;color:#222;margin-top:10px}
.news-item p{font-size:13px;line-height:1.5;color:var(--muted);margin:4px 0 6px}
.news-item a{font-size:13px;color:var(--orange);text-transform:uppercase;text-decoration:none}

/* footer */
.site-footer{position:absolute;left:0;top:2371px;width:1200px;height:365px;background:var(--black);color:var(--white)}
.footer-col{position:absolute;top:60px}
.footer-col h4{font-size:18px;font-weight:400;text-transform:uppercase;margin-bottom:14px}
.footer-col li{list-style:none;font-size:14px;line-height:28px}
.col-links{left:106px}.col-resources{left:303px}.col-contact{left:518px}
.social{display:flex;gap:16px;margin-top:18px}
.social span{width:36px;height:36px;border-radius:50%;background:var(--purple)}
.site-footer .brand-name{position:absolute;left:784px;top:74px}
.footer-rule{position:absolute;left:92px;top:288px;width:984px;height:1px;background:#333}
.copyright{position:absolute;left:0;top:321px;width:1200px;text-align:center;font-size:14px;color:#aaa}
</style>
</head>
<body>

<header class="site-header">
  <span class="brand-name">Pinewood and Harbour Financial Co-operative</span>
  <div class="header-phone">
    <svg width="22" height="22" viewBox="0 0 24 24"><path fill="#fbed22" d="M6.6 10.8a15 15 0 0 0 6.6 6.6l2.2-2.2a1 1 0 0 1 1-.25 11.4 11.4 0 0 0 3.6.57 1 1 0 0 1 1 1V20a1 1 0 0 1-1 1A17 17 0 0 1 3 4a1 1 0 0 1 1-1h3.5a1 1 0 0 1 1 1c0 1.25.2 2.45.57 3.57a1 1 0 0 1-.25 1z"/></svg>
    (555) 014-3870
  </div>
  <nav class="main-nav">
    <span>Apply Loan</span><span>Product &amp; Services</span><span>Tools &amp; Benefits</span><span>My Credit Union</span>
  </nav>
</header>

<section class="hero" role="img" aria-label="Photo of a woman dropping a coin into a pink piggy bank">
  <div class="hero-caption">
    <div class="kicker">Curabitur vel misit amet</div>
    <h1>Magna malesuada ultric</h1>
    <p>interdum vel blandit sed nulla In ullamcorper est<br>eget tempor cursus neque mi consec</p>
  </div>
  <div class="hero-dots"><span></span><span></span><span></span><span></span></div>
</section>

<section class="quick-actions">
  <div class="action">
    <svg viewBox="0 0 90 90" fill="none" stroke="#6b449b" stroke-width="2.5"><circle cx="45" cy="12" r="7"/><path d="M36 34v-6a9 9 0 0 1 18 0v6z"/><circle cx="18" cy="56" r="7"/><path d="M9 82v-10a9 9 0 0 1 18 0v10z"/><circle cx="72" cy="56" r="7"/><path d="M63 82v-10a9 9 0 0 1 18 0v10z"/><path d="M45 34v16M45 50L27 62M45 50l18 12"/></svg>
    <h2>Apply for Loan</h2>
    <p>Morbi diam mauris viverra in gravida eu mattis in ante Morbi eget arcu</p>
    <span class="btn">Click Here</span>
  </div>
  <div class="action">
    <svg viewBox="0 0 90 90" fill="none" stroke="#6b449b" stroke-width="2.5"><circle cx="48" cy="30" r="11"/><circle cx="68" cy="12" r="8"/><path d="M48 24v12M45 27h5a2 2 0 0 1 0 4h-4a2 2 0 0 0 0 4h5"/><path d="M6 66l12-6h14l12 4h-14M18 60l-12 16h40l36-18-6-4-22 10"/></svg>
    <h2>Become a Member</h2>
    <p>Morbi diam mauris viverra in gravida eu mattis in ante Morbi eget arcu</p>
    <span class="btn">Click Here</span>
  </div>
  <div class="action">
    <svg viewBox="0 0 90 90" fill="none" stroke="#6b449b" stroke-width="3"><rect x="25" y="4" width="40" height="82" rx="5"/><rect x="31" y="12" width="28" height="18"/><g fill="#6b449b" stroke="none"><rect x="31" y="38" width="7" height="7"/><rect x="41.5" y="38" width="7" height="7"/><rect x="52" y="38" width="7" height="7"/><rect x="31" y="50" width="7" height="7"/><rect x="41.5" y="50" width="7" height="7"/><rect x="52" y="50" width="7" height="7"/><rect x="31" y="62" width="7" height="7"/><rect x="41.5" y="62" width="7" height="7"/><rect x="52" y="62" width="7" height="7"/></g></svg>
    <h2>Financial Calculators</h2>
    <p>Morbi diam mauris viverra in gravida eu mattis in ante Morbi eget arcu</p>
    <span class="btn">Click Here</span>
  </div>
</section>

<section class="promo-band">
  <article class="promo-card credit-union">
    <div class="promo-photo" role="img" aria-label="Photo of a smiling young woman reading a letter at a desk"></div>
    <div class="promo-body">
      <h3>My Credit<br>Union</h3>
      <p>interdum vel blandit sed nulla In ullamcorper est eget tempor cursus neque mi cons</p>
      <span class="btn">Click Here</span>
    </div>
  </article>
  <article class="promo-card products">
    <div class="promo-photo" role="img" aria-label="Photo of a woman giving thumbs up beside a laptop"></div>
    <div class="promo-fill"></div>
    <div class="promo-body">
      <h3>Product &amp;<br>Services</h3>
      <p>interdum vel blandit sed nulla In ullamcorper est eget tempor cursus neque mi cons</p>
      <span class="btn">Click Here</span>
    </div>
  </article>
</section>

<section class="notice">
  <div class="notice-photo" role="img" aria-label="Photo of a smiling woman holding up a bank card"></div>
  <div class="notice-text">
    <h2>ATM Card Renewal Notice</h2>
    <p class="lead">Please b adviced that all ATM Cards issues Feb 2014<br>EXPIRES EFFECTIVE FEB 28, 2017</p>
    <p class="body">Curabitur vel mi sit amet magna malesuada ultrices Ut nisi erat<br>fermentum vel congue id euismod in elit Fusce</p>
    <span class="btn">Click Here</span>
  </div>
</section>

<section class="rates">
  <h2>Featured Rates</h2>
  <div class="rate">
    <svg viewBox="0 0 40 36" fill="none" stroke="#222" stroke-width="2"><circle cx="20" cy="10" r="7"/><path d="M6 34v-4a10 10 0 0 1 10-10h8a10 10 0 0 1 10 10v4z"/></svg>
    <span class="label">Consumer Loans<small>as low as</small></span><span class="value">9.00% ARP</span>
  </div>
  <div class="rate">
    <svg viewBox="0 0 40 36" fill="none" stroke="#222" stroke-width="3"><circle cx="8" cy="24" r="6"/><circle cx="32" cy="24" r="6"/><path d="M8 24l8-10h10l6 10M16 14l-2-4h-4M26 14l2-4h5"/></svg>
    <span class="label">New Auto/Motorcycle<small>as low as</small></span><span class="value">7.00% ARP</span>
  </div>
  <div class="rate">
    <svg viewBox="0 0 40 36" fill="none" stroke="#222" stroke-width="2"><path d="M4 26v-7l5-8h20l7 8v7z"/><circle cx="12" cy="27" r="4"/><circle cx="28" cy="27" r="4"/><path d="M10 19h22"/></svg>
    <span class="label">Used Auto/Motorcycle<small>as low as</small></span><span class="value">11.75% ARP</span>
  </div>
  <div class="rate">
    <svg viewBox="0 0 40 36" fill="none" stroke="#222" stroke-width="2"><path d="M4 18L20 4l16 14M9 14v20h22V14"/><path d="M15 28l10-10"/><circle cx="16" cy="20" r="2"/><circle cx="24" cy="27" r="2"/></svg>
    <span class="label">Mortgages<small>as low as</small></span><span class="value">8.25% ARP</span>
  </div>
</section>

<section class="news">
  <h2>News &amp; Events</h2>
  <div class="news-item">
    <div class="news-thumb" role="img" aria-label="Photo of a card being handed over a counter"></div>
    <div>
      <h3>Morbi diam mauris viverra</h3>
      <p>in gravida eu mattis in ante Morbi eget arcu Morbi porta libero id ullamcorper nonummy nibh ligula pulvinar metus eget</p>
      <a href="#">Read More</a>
    </div>
  </div>
  <div class="news-item">
    <div class="news-thumb" role="img" aria-label="Photo of people at a business event"></div>
    <div>
      <h3>Donec convallis pede</h3>
      <p>in gravida eu mattis in ante Morbi eget arcu Morbi porta libero id ullamcorper nonummy nibh ligula pulvinar metus eget</p>
      <a href="#">Read More</a>
    </div>
  </div>
</section>

<footer class="site-footer">
  <div class="footer-col col-links">
    <h4>Quick Links</h4>
    <ul><li>Home</li><li>Apply Now</li><li>My Credit Union</li><li>Product &amp; Services</li></ul>
  </div>
  <div class="footer-col col-resources">
    <h4>Resources</h4>
    <ul><li>Apply for Loan</li><li>Tools &amp; Benefits</li><li>Resources</li><li>Conact Us</li></ul>
  </div>
  <div class="footer-col col-contact">
    <h4>Contact Info</h4>
    <ul><li>The Harbour Commons Building</li><li>2217 Orchard Lane</li><li>Pinewood Falls, Vermont 05990</li><li>P:(555) 014-3870</li></ul>
    <div class="social" aria-label="Social media links"><span></span><span></span><span></span><span></span></div>
  </div>
  <span class="brand-name">Pinewood and Harbour Financial Co-operative</span>
  <div class="footer-rule"></div>
  <p class="copyright">© 2017 Company Name&nbsp; All right reserved&nbsp; Term of Use</p>
</footer>

</body>
</html>
```